TLK Electricial Contracting Services

Hi guys, after a design for my small electrical company, have logo design files to be incorporated into the layout, the basic concept is electrical contracting services for residential, commercial, industrial & data services, image is clean clear and strong,

Card format is to have a nice clean logo on front,with maybe the Residential – commercial – industrial - data, followed with licensed & insured, followed by contact details on backside of the card.

Target Market(s)

Residential, commercial, industrial sectors.

Industry/Entity Type

Electrical

Contact Information for Business Card

TLK logo,
Residential – commercial – industrial - data
REC: 61307
Email: tlk@vornamail.net.au
Phone: 0487 352 019

Requirements
Must have
• Clean & strong design.
Nice to have
• If possible, I would like the logo colours inverted so the text is orange and the background is black on the front of the card, then the backside of the card be the reverse colour
Should not have
• No Sparks, lightning bolts,

```html
<!DOCTYPE html>
<html lang="en">
<head>
<meta charset="utf-8">
<title>TLK Electrical – Business Card</title>
<link rel="stylesheet" href="https://fonts.googleapis.com/css2?family=Aldrich&display=swap">
<style>
  :root {
    --backdrop: #33434c;
    --card-black: #0b0b0b;
    --brand-orange: #f4832a;
    --white: #ffffff;
    --ink: #111111;
  }
  * { margin: 0; padding: 0; box-sizing: border-box; }
  html, body { width: 1200px; height: 900px; overflow: hidden; }
  body {
    background: var(--backdrop);
    font-family: "Aldrich", "Arial", sans-serif;
    position: relative;
  }
  .card {
    position: absolute;
    left: 280px;
    width: 640px;
    height: 366px;
    overflow: hidden;
    box-shadow: 0 12px 30px rgba(0,0,0,0.35);
  }
  .card--front { top: 60px; background: var(--card-black); }
  .card--back  { top: 474px; background: var(--brand-orange); }

  .brand { position: absolute; text-align: center; }
  .brand__name {
    font-size: 96px;
    line-height: 1;
    letter-spacing: 2px;
  }
  .brand__tag { font-size: 22px; letter-spacing: 0.5px; margin-top: 4px; }

  .card--front .brand { left: 0; right: 0; top: 26px; }
  .card--front .brand__name { color: var(--brand-orange); }
  .card--front .brand__tag { color: var(--white); }

  .rule { position: absolute; left: 0; right: 0; height: 3px; }
  .card--front .rule { background: var(--brand-orange); }
  .rule--top { top: 172px; }
  .rule--bottom { top: 282px; }

  .edge-block {
    position: absolute; top: 218px; width: 20px; height: 30px;
    background: var(--brand-orange);
  }
  .edge-block--left { left: 0; }
  .edge-block--right { right: 0; }

  .person { position: absolute; left: 34px; top: 208px; }
  .person__name { color: var(--brand-orange); font-size: 24px; letter-spacing: 0.5px; }
  .person__role { color: var(--white); font-size: 14px; margin-top: 2px; }

  .contacts {
    position: absolute; right: 34px; top: 206px;
    color: var(--brand-orange); font-size: 15px; text-align: right;
    line-height: 24px;
  }
  .contacts__row { display: flex; justify-content: flex-end; align-items: center; gap: 8px; }
  .contacts__icon { width: 14px; height: 14px; fill: var(--white); }

  .footer-strip { position: absolute; left: 0; right: 0; bottom: 0; height: 66px; }
  .card--front .footer-strip { background: var(--brand-orange); }
  .footer-strip__bar {
    position: absolute; left: 0; top: 4px; width: 330px; height: 12px;
    background: var(--white);
    border: 2px solid var(--card-black);
    border-left: none;
  }

  .card--back .brand { right: 36px; top: 32px; text-align: right; }
  .card--back .brand__name { color: var(--ink); text-align: center; }
  .card--back .brand__tag { color: var(--ink); }

  .services {
    position: absolute; left: 44px; top: 248px;
    color: var(--ink); font-size: 18px; line-height: 24px;
  }
  .card--back .rule { top: 308px; background: var(--ink); }
  .card--back .footer-strip { height: 50px; background: var(--card-black); }
  .card--back .footer-strip__bar { background: var(--white); border-color: var(--brand-orange); top: 2px; }
</style>
</head>
<body>

<section class="card card--front" aria-label="Card front">
  <div class="brand">
    <div class="brand__name">TLK</div>
    <div class="brand__tag">Tarlow Kent Electrical</div>
  </div>
  <div class="rule rule--top"></div>
  <div class="edge-block edge-block--left"></div>
  <div class="person">
    <div class="person__name">Dale Harper</div>
    <div class="person__role">Owner</div>
  </div>
  <div class="contacts">
    <div class="contacts__row">
      <span>0487 352 019</span>
      <svg class="contacts__icon" viewBox="0 0 24 24" aria-hidden="true"><path d="M6.6 10.8a15.2 15.2 0 0 0 6.6 6.6l2.2-2.2c.3-.3.7-.4 1-.2 1.1.4 2.3.6 3.6.6.6 0 1 .4 1 1V20c0 .6-.4 1-1 1A17 17 0 0 1 3 4c0-.6.4-1 1-1h3.5c.6 0 1 .4 1 1 0 1.3.2 2.5.6 3.6.1.3 0 .7-.2 1z"/></svg>
    </div>
    <div class="contacts__row">
      <span>tlk@vornamail.net.au</span>
      <svg class="contacts__icon" viewBox="0 0 24 24" aria-hidden="true"><path d="M2 5h20v14H2zm2 2v.4l8 5 8-5V7zm0 2.8V17h16V9.8l-8 5z"/></svg>
    </div>
  </div>
  <div class="edge-block edge-block--right"></div>
  <div class="rule rule--bottom"></div>
  <div class="footer-strip"><div class="footer-strip__bar"></div></div>
</section>

<section class="card card--back" aria-label="Card back">
  <div class="brand">
    <div class="brand__name">TLK</div>
    <div class="brand__tag">Tarlow Kent Electrical</div>
  </div>
  <div class="services">
    <div>licenced &amp; insured Residential</div>
    <div>commercial - industrial - data REC: 61307</div>
  </div>
  <div class="rule"></div>
  <div class="footer-strip"><div class="footer-strip__bar"></div></div>
</section>

</body>
</html>
```